Stationery Set for Velmora Company

I need to create full stationery design for my company; Business Cards, Envelops, Letter Heads, Calendar.
In the letter head and Envelops... only contact information and website links.
Our company is a Service Management company with different domains of innovative services including Technology Service Management, Education Services, Outsourcing Management, Events Management.
I need a modern and innovative design specially for the business card. I some transparent designs and I like it, but don't limit your innovation to what I mentioned. Sky is limit for your innovation.

Target Market(s)

Middle East & Africa

Industry/Entity Type

Business Management

Colors
34a7d8
0355a3
85acd3
86cae7
cee9f5
cfdeed
e4daeb
f3f1f8
ecf7fb

Requirements
Must have
• Name, Title, Email, Mobile
Nice to have
• We have multiple locations in USA, KSA, EGY, so I need ideas about how to include all contact details maybe QR / Barcode or something else.
• Please see our locations and contact information: www.brightvelmora.example
Should not have
• Too much text

```html
<!DOCTYPE html>
<html lang="en">
<head>
<meta charset="utf-8">
<title>Velmora Company – Business Card</title>
<link href="https://fonts.googleapis.com/css2?family=Arimo:wght@400;700&display=swap" rel="stylesheet">
<style>
  :root {
    --brand-blue: #3d6db6;
    --brand-blue-deep: #2f5ea8;
    --paper: #ffffff;
    --ink: #1f1f1f;
    --stage: #e9ecf1;
  }
  * { box-sizing: border-box; margin: 0; padding: 0; }
  html, body { width: 1200px; height: 750px; overflow: hidden; }
  body {
    background: var(--stage);
    font-family: "Arimo", Arial, sans-serif;
    display: flex;
    align-items: center;
    justify-content: center;
    gap: 40px;
  }
  .card {
    width: 540px;
    height: 310px;
    position: relative;
    overflow: hidden;
    flex-shrink: 0;
    box-shadow: 0 10px 30px rgba(0,0,0,.18);
  }

  /* Front */
  .card-front {
    background: var(--brand-blue);
    display: flex;
    align-items: center;
    justify-content: center;
  }
  .wordmark {
    display: flex;
    align-items: center;
    gap: 12px;
    font-weight: 700;
    font-size: 36px;
    letter-spacing: .5px;
    white-space: nowrap;
  }
  .card-front .wordmark { color: var(--paper); }
  .wordmark-dot {
    width: 16px; height: 16px; border-radius: 50%;
    background: currentColor;
    flex-shrink: 0;
  }

  /* Back */
  .card-back { background: var(--paper); }
  .band {
    position: absolute; left: 0; right: 0;
    background: var(--brand-blue);
    color: var(--paper);
    display: flex; align-items: center;
    white-space: nowrap;
  }
  .band-top { top: 0; height: 44px; padding: 0 26px; }
  .band-bottom {
    bottom: 0; height: 38px;
    padding: 0 18px;
    justify-content: space-between;
    font-size: 11.5px;
  }
  .band-bottom span { white-space: nowrap; }
  .holder-name { font-weight: 700; font-size: 17px; letter-spacing: .3px; }
  .holder-title { font-size: 15px; margin-left: 8px; }
  .band-bottom b { font-weight: 700; margin-right: 4px; }

  .card-back .wordmark {
    position: absolute; left: 28px; top: 150px;
    color: var(--brand-blue-deep);
    font-size: 22px;
    gap: 9px;
  }
  .card-back .wordmark-dot { width: 12px; height: 12px; }
  .offices {
    position: absolute; left: 300px; top: 60px;
    font-size: 12px; line-height: 1.42; color: var(--ink);
    white-space: nowrap;
  }
  .office { font-style: normal; }
  .office + .office { margin-top: 8px; }
  .phone-line { display: flex; align-items: center; gap: 6px; }
  .phone-icon { width: 12px; height: 12px; fill: var(--brand-blue-deep); }
</style>
</head>
<body>

  <section class="card card-front" aria-label="Business card front">
    <div class="wordmark"><span class="wordmark-dot"></span>Velmora Company</div>
  </section>

  <section class="card card-back" aria-label="Business card back">
    <header class="band band-top">
      <span class="holder-name">KARIM HADDAD</span>
      <span class="holder-title">-&nbsp; President</span>
    </header>

    <div class="wordmark"><span class="wordmark-dot"></span>Velmora Company</div>

    <div class="offices">
      <address class="office">
        118 Harbor Crest Lane<br>
        4th Floor Linden Bay<br>
        CA 90210 US<br>
        <span class="phone-line">
          <svg class="phone-icon" viewBox="0 0 24 24"><path d="M6.6 10.8a15 15 0 0 0 6.6 6.6l2.2-2.2a1 1 0 0 1 1-.25 11.4 11.4 0 0 0 3.6.57 1 1 0 0 1 1 1V20a1 1 0 0 1-1 1A17 17 0 0 1 3 4a1 1 0 0 1 1-1h3.5a1 1 0 0 1 1 1c0 1.25.2 2.45.57 3.57a1 1 0 0 1-.25 1z"/></svg>
          +1.555 010 2470
        </span>
      </address>
      <address class="office">
        Riyadh, Al Nakheel,<br>
        Wadi Noor St.<br>
        Qamar Towers<br>
        Block 3C 1st Floor A12, A14<br>
        <span class="phone-line">
          <svg class="phone-icon" viewBox="0 0 24 24"><path d="M6.6 10.8a15 15 0 0 0 6.6 6.6l2.2-2.2a1 1 0 0 1 1-.25 11.4 11.4 0 0 0 3.6.57 1 1 0 0 1 1 1V20a1 1 0 0 1-1 1A17 17 0 0 1 3 4a1 1 0 0 1 1-1h3.5a1 1 0 0 1 1 1c0 1.25.2 2.45.57 3.57a1 1 0 0 1-.25 1z"/></svg>
          +966 55500 10 30
        </span>
      </address>
    </div>

    <footer class="band band-bottom">
      <span><b>P :</b>+1.555 010 2470</span>
      <span><b>E :</b>info@brightvelmora.example</span>
      <span><b>W :</b>www.brightvelmora.example</span>
    </footer>
  </section>

</body>
</html>
```